New Business Card Design Project

Use the flyer uploaded and website www.brightoakbuilders.com for inspiration.
List Our Services on Backside of business cards
Marcus Delling
Harborline Builders Inc.
Licensed General Contractors
858-471-6093

Contact Information for Business Card

Use the flyer uploaded and website www.brightoakbuilders.com for inspiration. List Our Services on Backside of business cards Marcus Delling Harborline Builders Inc. Licensed General Contractors 858-471-6093

```html
<!DOCTYPE html>
<html lang="en">
<head>
<meta charset="utf-8">
<title>Harborline Builders – Business Cards</title>
<link rel="stylesheet" href="https://fonts.googleapis.com/css2?family=Lato:wght@300;400;700;900&display=swap">
<style>
  :root {
    --ink: #141414;
    --paper: #ffffff;
    --brand-blue: #3a86cf;
    --accent-red: #e5212f;
    --backdrop: #2b2b2d;
    --muted: #2a2a2a;
  }
  * { box-sizing: border-box; margin: 0; padding: 0; }
  html, body { width: 1200px; height: 900px; overflow: hidden; }
  body {
    background: var(--backdrop);
    font-family: "Lato", sans-serif;
    display: flex;
    align-items: center;
    justify-content: center;
    gap: 70px;
  }
  .card {
    position: relative;
    width: 400px;
    height: 700px;
    overflow: hidden;
    box-shadow: 0 14px 40px rgba(0,0,0,.55);
  }
  .card--front { background: var(--paper); }
  .card--back { background: var(--ink); }

  .card__head {
    position: absolute;
    left: 0; top: 0; right: 0;
    height: 230px;
    display: flex;
    align-items: center;
    justify-content: center;
  }
  .card--front .card__head { background: var(--ink); }
  .card--back .card__head { background: var(--paper); }

  .wordmark {
    font-weight: 300;
    font-size: 25px;
    letter-spacing: 3px;
    text-transform: uppercase;
    text-align: center;
    line-height: 1.3;
  }
  .card--front .wordmark { color: var(--paper); }
  .card--back .wordmark { color: var(--ink); }

  .frame {
    position: absolute;
    left: 20px; top: 205px;
    right: -20px; bottom: 22px;
    border: 7px solid var(--brand-blue);
  }
  .card--front .panel {
    position: absolute;
    left: 27px; top: 212px; right: 0; bottom: 29px;
    background: var(--paper);
  }

  .content {
    position: absolute;
    left: 58px; right: 24px;
    top: 268px;
  }

  .name {
    color: var(--brand-blue);
    font-weight: 900;
    font-size: 40px;
    letter-spacing: .5px;
    text-transform: uppercase;
    line-height: 1;
  }
  .role {
    color: var(--accent-red);
    font-size: 22px;
    font-weight: 400;
    margin-top: 6px;
  }
  .rule {
    width: 44px; height: 3px;
    background: var(--brand-blue);
    margin: 22px 0 20px;
  }
  .contact-list { list-style: none; }
  .contact-list li {
    display: flex;
    align-items: center;
    gap: 12px;
    font-size: 19px;
    color: var(--muted);
    line-height: 1;
    margin-bottom: 13px;
    white-space: nowrap;
  }
  .contact-list svg { width: 18px; height: 18px; flex: none; }
  .license {
    color: var(--accent-red);
    font-weight: 700;
    font-size: 24px;
    letter-spacing: .3px;
  }

  .services-title {
    color: var(--brand-blue);
    font-weight: 900;
    font-size: 38px;
    text-transform: uppercase;
    line-height: 1;
  }
  .services-sub {
    color: var(--accent-red);
    font-size: 20px;
    margin-top: 6px;
  }
  .service-list { list-style: none; }
  .service-list li {
    display: flex;
    align-items: center;
    gap: 12px;
    color: var(--paper);
    font-size: 17.5px;
    line-height: 1;
    margin-bottom: 12px;
    white-space: nowrap;
  }
  .service-list svg { width: 18px; height: 18px; flex: none; }
</style>
</head>
<body>

  <article class="card card--front" aria-label="Business card front">
    <div class="frame"></div>
    <div class="panel"></div>
    <header class="card__head">
      <p class="wordmark">Harborline<br>Builders</p>
    </header>
    <div class="content">
      <h1 class="name">Marcus Delling</h1>
      <p class="role">Licensed General Contractors</p>
      <div class="rule"></div>
      <ul class="contact-list">
        <li>
          <svg viewBox="0 0 24 24" aria-hidden="true"><path fill="var(--accent-red)" d="M6.6 10.8a15.1 15.1 0 0 0 6.6 6.6l2.2-2.2c.3-.3.7-.4 1-.2 1.1.4 2.3.6 3.6.6.6 0 1 .4 1 1V20c0 .6-.4 1-1 1A17 17 0 0 1 3 4c0-.6.4-1 1-1h3.5c.6 0 1 .4 1 1 0 1.3.2 2.5.6 3.6.1.3 0 .7-.2 1z"/></svg>
          858-471-6093 Call/Text
        </li>
        <li>
          <svg viewBox="0 0 24 24" aria-hidden="true"><rect x="2" y="5" width="20" height="14" rx="1.5" fill="var(--accent-red)"/><path d="M3 6l9 7 9-7" fill="none" stroke="#fff" stroke-width="1.6"/></svg>
          info@brightoakbuilders.com
        </li>
        <li>
          <svg viewBox="0 0 24 24" aria-hidden="true"><circle cx="12" cy="12" r="10" fill="var(--accent-red)"/><path d="M2 12h20M12 2c3 3 3 17 0 20M12 2c-3 3-3 17 0 20" fill="none" stroke="#fff" stroke-width="1.4"/></svg>
          brightoakbuilders.com
        </li>
        <li>
          <svg viewBox="0 0 24 24" aria-hidden="true"><path fill="var(--accent-red)" d="M12 2a7 7 0 0 0-7 7c0 5 7 13 7 13s7-8 7-13a7 7 0 0 0-7-7z"/><circle cx="12" cy="9" r="2.6" fill="#fff"/></svg>
          Harborline Builders Inc.
        </li>
      </ul>
      <div class="rule"></div>
      <p class="license">CSLB LIC: #1048261</p>
    </div>
  </article>

  <article class="card card--back" aria-label="Business card back">
    <div class="frame"></div>
    <header class="card__head">
      <p class="wordmark">Harborline<br>Builders</p>
    </header>
    <div class="content">
      <h2 class="services-title">Our Services</h2>
      <p class="services-sub">Specializing In</p>
      <div class="rule"></div>
      <ul class="service-list">
        <li><svg viewBox="0 0 24 24" aria-hidden="true"><circle cx="12" cy="12" r="11" fill="var(--brand-blue)"/><path d="M7 12l3.5 3.5L17 9" fill="none" stroke="var(--ink)" stroke-width="2.4"/></svg>Remodel Kitchen &amp; Bath</li>
        <li><svg viewBox="0 0 24 24" aria-hidden="true"><circle cx="12" cy="12" r="11" fill="var(--brand-blue)"/><path d="M7 12l3.5 3.5L17 9" fill="none" stroke="var(--ink)" stroke-width="2.4"/></svg>Painting Interior &amp; Exterior</li>
        <li><svg viewBox="0 0 24 24" aria-hidden="true"><circle cx="12" cy="12" r="11" fill="var(--brand-blue)"/><path d="M7 12l3.5 3.5L17 9" fill="none" stroke="var(--ink)" stroke-width="2.4"/></svg>Flooring Carpet, Vinyl, Wood</li>
        <li><svg viewBox="0 0 24 24" aria-hidden="true"><circle cx="12" cy="12" r="11" fill="var(--brand-blue)"/><path d="M7 12l3.5 3.5L17 9" fill="none" stroke="var(--ink)" stroke-width="2.4"/></svg>Window &amp; Door Replacement</li>
        <li><svg viewBox="0 0 24 24" aria-hidden="true"><circle cx="12" cy="12" r="11" fill="var(--brand-blue)"/><path d="M7 12l3.5 3.5L17 9" fill="none" stroke="var(--ink)" stroke-width="2.4"/></svg>Plumbing Repairs &amp; Upgrades</li>
        <li><svg viewBox="0 0 24 24" aria-hidden="true"><circle cx="12" cy="12" r="11" fill="var(--brand-blue)"/><path d="M7 12l3.5 3.5L17 9" fill="none" stroke="var(--ink)" stroke-width="2.4"/></svg>Energy-Efficient Upgrades</li>
        <li><svg viewBox="0 0 24 24" aria-hidden="true"><circle cx="12" cy="12" r="11" fill="var(--brand-blue)"/><path d="M7 12l3.5 3.5L17 9" fill="none" stroke="var(--ink)" stroke-width="2.4"/></svg>Deck &amp; Patio Construction</li>
        <li><svg viewBox="0 0 24 24" aria-hidden="true"><circle cx="12" cy="12" r="11" fill="var(--brand-blue)"/><path d="M7 12l3.5 3.5L17 9" fill="none" stroke="var(--ink)" stroke-width="2.4"/></svg>Water &amp; Mold Damage</li>
        <li><svg viewBox="0 0 24 24" aria-hidden="true"><circle cx="12" cy="12" r="11" fill="var(--brand-blue)"/><path d="M7 12l3.5 3.5L17 9" fill="none" stroke="var(--ink)" stroke-width="2.4"/></svg>Garage Renovation</li>
      </ul>
    </div>
  </article>

</body>
</html>
```